Website and Mobile Devices design for food related application.

We need a design that is simple yet playful. The design should be food related if possible.
This design will be on the website and the mobile platform markets we intend application to be deployed too.
This application/website is called "Forkwizo[.com]. Its a random restaurant picker for the indecisive users.
Updates
Hi all, I picked a design. Again lots of great designs were submitted but I picked one that was more in line with what I wanted.
Target Market(s)
young internet savvy users.
Industry/Entity Type
Restaurant
Look and feel
Each slider illustrates characteristics of the customer's brand and the style your logo design should communicate.

```html
<!DOCTYPE html>
<html lang="en">
<head>
<meta charset="utf-8">
<title>Forkwizo – Contact Us</title>
<link href="https://fonts.googleapis.com/css2?family=Arimo:wght@400;700&family=Source+Sans+3:wght@400;600&display=swap" rel="stylesheet">
<style>
  :root{
    --page-bg:#ececec;
    --status-bg:#1d1d1d;
    --status-text:#ffffff;
    --header-top:#6d92bb;
    --header-bottom:#3f6a98;
    --band-top:#5d80b0;
    --band-bottom:#4d70a4;
    --accent:#f39a1e;
    --content-bg:#f3f6f9;
    --label:#35359a;
    --field-border:#b9b9b9;
    --field-bg:#ffffff;
    --tab-top:#5a93c9;
    --tab-bottom:#3c76b3;
    --tab-active:#2b5796;
    --tab-text:#0d1b8a;
    --icon:#ffffff;
  }
  *{box-sizing:border-box;margin:0;padding:0}
  html,body{width:1200px;height:1000px;overflow:hidden;background:var(--page-bg)}
  body{position:relative;font-family:"Arimo",Arial,sans-serif}
  .screen{
    position:absolute;left:293px;top:38px;width:384px;height:577px;
    transform:scale(1.6);transform-origin:0 0;
    background:var(--content-bg);overflow:hidden;
    box-shadow:0 0 2px rgba(0,0,0,.25);
  }
  .status-bar{position:absolute;left:0;top:0;width:384px;height:22px;background:linear-gradient(#3a3a3a,var(--status-bg));color:var(--status-text);font-weight:700;font-size:13px}
  .status-bar .signal{position:absolute;left:4px;top:6px}
  .status-bar .carrier{position:absolute;left:28px;top:4px}
  .status-bar .time{position:absolute;left:0;right:0;top:3px;text-align:center;font-size:15px}
  .status-bar .battery{position:absolute;right:4px;top:5px}
  .divider{position:absolute;left:0;width:384px;height:4px;background:#fff}
  .app-header{position:absolute;left:0;top:28px;width:384px;height:48px;background:linear-gradient(var(--header-top),var(--header-bottom))}
  .refresh{position:absolute;left:6px;top:13px}
  .search-pill{position:absolute;left:35px;top:9px;width:343px;height:31px;border-radius:16px;background:linear-gradient(#fff 60%,#e6e6e6);box-shadow:inset 0 1px 2px rgba(0,0,0,.35)}
  .search-pill .magnifier{position:absolute;left:6px;top:7px}
  .search-pill .sep{position:absolute;left:29px;top:3px;height:25px;border-left:1px dashed #888}
  .search-pill .query{position:absolute;left:43px;top:7px;font-size:15px;color:#111}
  .search-pill .brand-dot{position:absolute;right:10px;top:8px;width:15px;height:15px;border-radius:50%;background:var(--accent)}
  .title-band{position:absolute;left:0;top:78px;width:384px;height:36px;background:linear-gradient(var(--band-top),var(--band-bottom));color:var(--accent);font-family:"Source Sans 3",sans-serif;font-size:19px;text-align:center;line-height:36px}
  .contact-form{position:absolute;left:76px;top:160px;width:233px}
  .field-label{display:block;font-size:10px;color:var(--label);margin:0 0 2px 2px}
  .field{display:block;width:232px;height:25px;background:var(--field-bg);border:2px solid var(--field-border);border-top-color:#cfcfcf;box-shadow:inset 1px 1px 2px rgba(0,0,0,.15)}
  .field + .field-label{margin-top:19px}
  .field.message{height:152px}
  .submit{position:absolute;left:173px;top:287px;width:60px;height:21px;border-radius:2px;border:1px solid #e0b060;background:linear-gradient(#fde7b8,#f5b24d);font-size:9px;color:#222;text-align:center;line-height:19px}
  .tab-bar{position:absolute;left:0;top:524px;width:384px;height:53px;background:linear-gradient(var(--tab-top) 50%,var(--tab-bottom) 50%);display:flex}
  .tab{flex:1;position:relative;text-align:center;color:var(--tab-text);font-size:11.5px}
  .tab svg{position:absolute;left:50%;top:8px;transform:translateX(-50%)}
  .tab .tab-label{position:absolute;left:0;right:0;top:37px}
  .tab.is-active{background:var(--tab-active);color:var(--accent);font-weight:700}
</style>
</head>
<body>
<main class="screen">
  <div class="status-bar">
    <svg class="signal" width="22" height="10" viewBox="0 0 22 10"><rect x="0" y="7" width="3" height="3" fill="#fff"/><rect x="4" y="5" width="3" height="5" fill="#fff"/><rect x="8" y="3" width="3" height="7" fill="#fff"/><rect x="12" y="1" width="3" height="9" fill="#fff"/><rect x="16" y="0" width="3" height="10" fill="#fff"/></svg>
    <span class="carrier">Carrier</span>
    <span class="time">6:40 PM</span>
    <svg class="battery" width="26" height="12" viewBox="0 0 26 12"><rect x="0.5" y="0.5" width="22" height="11" rx="2" fill="none" stroke="#ccc"/><rect x="2" y="2" width="19" height="8" fill="#eee"/><rect x="23" y="3.5" width="2.5" height="5" fill="#ccc"/></svg>
  </div>
  <div class="divider" style="top:22px;height:6px"></div>

  <header class="app-header">
    <svg class="refresh" width="22" height="22" viewBox="0 0 22 22" fill="none" stroke="#fff" stroke-width="2.4"><path d="M4 9a7.5 7.5 0 0 1 13-2"/><path d="M18 13a7.5 7.5 0 0 1-13 2"/><path d="M17.5 2v5h-5" stroke-width="2"/><path d="M4.5 20v-5h5" stroke-width="2"/></svg>
    <div class="search-pill">
      <svg class="magnifier" width="18" height="18" viewBox="0 0 18 18" fill="none" stroke="#555" stroke-width="2.4"><circle cx="7.5" cy="7.5" r="5.5"/><path d="M11.5 11.5l5 5"/></svg>
      <span class="sep"></span>
      <span class="query">Forkwizo</span>
      <span class="brand-dot"></span>
    </div>
  </header>
  <div class="divider" style="top:76px;height:2px"></div>

  <h1 class="title-band">Contact Us</h1>

  <form class="contact-form">
    <label class="field-label">Name</label>
    <span class="field"></span>
    <label class="field-label">Email</label>
    <span class="field"></span>
    <label class="field-label">Message</label>
    <span class="field message"></span>
    <span class="submit">Submit</span>
  </form>

  <nav class="tab-bar">
    <div class="tab">
      <svg width="16" height="26" viewBox="0 0 16 26"><path d="M8 25C3 16 1 12 1 8a7 7 0 0 1 14 0c0 4-2 8-7 17z" fill="#fff"/><circle cx="8" cy="8" r="2.5" fill="#222"/></svg>
      <span class="tab-label">Stations</span>
    </div>
    <div class="tab">
      <svg width="22" height="26" viewBox="0 0 22 26"><circle cx="11" cy="7" r="6" fill="#fff" stroke="#999"/><path d="M6 12h10l-2 4H8z" fill="#eee" stroke="#999"/><path d="M11 16v9" stroke="#777" stroke-width="1.5"/></svg>
      <span class="tab-label">Map</span>
    </div>
    <div class="tab">
      <svg width="24" height="24" viewBox="0 0 24 24"><path d="M12 1l3.2 7.2 7.8.7-5.9 5.2 1.8 7.7L12 17.8 5.1 21.8l1.8-7.7L1 8.9l7.8-.7z" fill="#fff"/></svg>
      <span class="tab-label">Favoris</span>
    </div>
    <div class="tab">
      <svg width="28" height="22" viewBox="0 0 28 22"><rect x="1" y="2" width="26" height="18" rx="1.5" fill="#fff" stroke="#222" stroke-width="1.5"/><rect x="1" y="6" width="26" height="4" fill="#222"/><rect x="4" y="13" width="8" height="3" fill="#222"/></svg>
      <span class="tab-label">Reservation</span>
    </div>
    <div class="tab is-active">
      <svg width="24" height="24" viewBox="0 0 24 24"><path d="M5 2l4 1 1.5 5-2.5 2a12 12 0 0 0 6 6l2-2.5 5 1.5 1 4-3 2C11 21 3 13 3 5z" fill="#fff"/></svg>
      <span class="tab-label">Contact</span>
    </div>
  </nav>
</main>
</body>
</html>
```